Termite Mailer September 2021

We need a clean modern looking flyer advertising termites via the mail.

Size should be 9"x6"

Our tagline is "The Smarter Approach to Pest Control"

Something along the stylistic design of these:

https://pics.lumora-share.net/Qk82vLmTzPwX4rNa1

https://pics.lumora-share.net/Hd37nBcYxTqW9sKe5

https://pics.lumora-share.net/Zr61pMfVaLuE2jGo8

https://www.cardvistaprint.net/wp-content/uploads/designs/img/Pest-Prevention-Postcard-PST-1003.jpg

Should include some of this verbiage:

HAVE YOU SCHEDULED YOUR ANNUAL TERMITE INSPECTION? - MAKE IT IN RED

DON'T WAIT. PROTECT YOUR HOME TODAY!

ABSOLUTELY FREE INSPECTION. NO OBLIGATION.

TERMITES CAN CAUSE SEVERE DAMAGE TO YOUR HOME.

BRIMVALE LOGO

THE SMARTER APPROACH TO PEST CONTROL.

PROTECT YOUR MOST VALUABLE ASSET.

10% DISCOUNT ON ANY SERVICE GUARANTEED IF YOU CALL TODAY.

INCLUDE A PICTURE OF A TERMITE AS WELL SOMEWHERE AND WOOD DAMAGE.

Target Market(s)

Homeowners in Southern California USA

Industry/Entity Type

Pest Control/Extermination

Font styles to use
Other font styles liked:
• Chaparral Pro Italic, Brava Slab

Requirements
Must have
• Clean design, picture of house, picture of Termite, 10% off coupon and call to action on the back
Should not have
• Bad looking houses, colors that don't match our logo

```html
<!DOCTYPE html>
<html lang="en">
<head>
<meta charset="utf-8">
<title>Brimvale Pest Control – Termite Mailer</title>
<link rel="stylesheet" href="https://fonts.googleapis.com/css2?family=Alegreya:ital,wght@0,700;0,800;1,400&family=Roboto+Condensed:wght@300;400&family=Roboto:wght@700&display=swap">
<style>
  :root {
    --backdrop: #575757;
    --card: #ffffff;
    --brand-blue: #0f6db8;
    --brand-blue-dark: #0b5fa5;
    --brand-green: #5cb53a;
    --brand-green-dark: #3a8a26;
    --alert-red: #e0202a;
    --ink: #1e1e1e;
  }
  * { box-sizing: border-box; margin: 0; padding: 0; }
  html, body { width: 1200px; height: 1000px; overflow: hidden; }
  body { background: var(--backdrop); position: relative; font-family: "Alegreya", Georgia, serif; }

  .card { position: absolute; left: 255px; width: 690px; height: 464px; background: var(--card); overflow: hidden; }
  .card--front { top: 16px; }
  .card--back { top: 513px; }
  .card-shapes { position: absolute; inset: 0; }

  /* Front */
  .headline {
    position: absolute; left: 355px; top: 22px;
    color: #fff; font-weight: 800; font-size: 37px; line-height: 45px; letter-spacing: 0.5px;
  }
  .subhead {
    position: absolute; left: 357px; top: 320px;
    color: var(--brand-blue); font-weight: 800; font-size: 23px; line-height: 30px;
  }
  .brand {
    position: absolute; display: flex; align-items: center; gap: 7px;
    font-family: "Roboto", Arial, sans-serif; font-weight: 700; color: var(--brand-blue);
  }
  .brand-dot { width: 30px; height: 30px; border-radius: 50%; background: var(--brand-blue); }
  .card--front .brand { left: 74px; top: 408px; font-size: 23px; }
  .tagline {
    position: absolute; left: 322px; top: 408px;
    font-style: italic; font-weight: 400; font-size: 21px; color: var(--brand-blue);
  }

  /* Back */
  .offer {
    position: absolute; left: 0; top: 272px; width: 340px; text-align: center; color: #fff;
  }
  .offer-title { font-weight: 800; font-size: 38px; line-height: 42px; text-shadow: 0 2px 3px rgba(0,0,0,.35); }
  .offer-line { font-family: "Roboto Condensed", Arial, sans-serif; font-weight: 300; font-size: 20px; line-height: 24px; }
  .offer-line--large { font-size: 29px; line-height: 34px; }
  .phone-pill {
    position: absolute; left: 23px; top: 385px; width: 290px; height: 52px;
    border: 2px solid #fff; border-radius: 26px; color: #fff;
    display: flex; align-items: center; justify-content: center;
    font-family: "Roboto", Arial, sans-serif; font-weight: 700; font-size: 30px;
  }
  .card--back .brand { left: 502px; top: 35px; font-size: 20px; }
  .card--back .brand-dot { width: 27px; height: 27px; }
  .benefits { position: absolute; left: 405px; top: 99px; list-style: none; }
  .benefit {
    position: relative; padding-left: 33px; margin-bottom: 11px;
    font-family: "Roboto Condensed", Arial, sans-serif; font-weight: 400; font-size: 19px; line-height: 25px;
    color: var(--ink); text-transform: uppercase;
  }
  .benefit svg { position: absolute; left: 0; top: 3px; }
  .website {
    position: absolute; left: 402px; top: 418px; display: flex; align-items: center; gap: 20px;
    color: #fff; font-weight: 700; font-size: 18px;
  }
</style>
</head>
<body>

<section class="card card--front">
  <svg class="card-shapes" width="690" height="464" viewBox="0 0 690 464">
    <defs>
      <linearGradient id="photoFade" x1="0" y1="0" x2="0" y2="1">
        <stop offset="0" stop-color="#e6e9ee"/>
        <stop offset="0.6" stop-color="#d6dde6"/>
        <stop offset="1" stop-color="#ffffff"/>
      </linearGradient>
    </defs>
    <rect x="0" y="0" width="330" height="420" fill="url(#photoFade)" role="img" aria-label="Technician in blue overalls spraying termite treatment along a wall"/>
    <polygon points="325,0 690,0 690,309 293,309" fill="var(--brand-blue)"/>
    <circle cx="600" cy="170" r="44" fill="#f3ece4" role="img" aria-label="Termite"/>
    <circle cx="600" cy="170" r="44" fill="none" stroke="var(--alert-red)" stroke-width="9"/>
    <line x1="569" y1="139" x2="631" y2="201" stroke="var(--alert-red)" stroke-width="9"/>
  </svg>
  <h1 class="headline">HAVE YOU<br>SCHEDULED<br>YOUR<br>ANNUAL<br>TERMITE<br>INSPECTION?</h1>
  <p class="subhead">DON'T WAIT. PROTECT<br>YOUR HOME TODAY!</p>
  <div class="brand"><span class="brand-dot"></span>BRIMVALE</div>
  <p class="tagline">The Smarter Approach to Pest Control</p>
</section>

<section class="card card--back">
  <svg class="card-shapes" width="690" height="464" viewBox="0 0 690 464">
    <defs>
      <linearGradient id="houseTone" x1="0" y1="0" x2="0" y2="1">
        <stop offset="0" stop-color="#5c9be0"/>
        <stop offset="0.55" stop-color="#b8b0a2"/>
        <stop offset="1" stop-color="#4f8a2e"/>
      </linearGradient>
      <linearGradient id="offerGreen" x1="0" y1="0" x2="1" y2="1">
        <stop offset="0" stop-color="var(--brand-green)"/>
        <stop offset="1" stop-color="var(--brand-green-dark)"/>
      </linearGradient>
    </defs>
    <polygon points="0,0 400,0 357,252 0,252" fill="url(#houseTone)" role="img" aria-label="Two-storey suburban home with green lawn under blue sky"/>
    <polygon points="0,250 357,250 320,464 0,464" fill="url(#offerGreen)"/>
    <polygon points="330,407 690,407 690,464 320,464" fill="var(--brand-blue)"/>
  </svg>

  <div class="offer">
    <p class="offer-title">10% DISCOUNT</p>
    <p class="offer-line">ON ANY SERVICE GUARANTEED</p>
    <p class="offer-line offer-line--large">IF YOU CALL TODAY</p>
  </div>
  <div class="phone-pill">+1 714-555-0182</div>

  <div class="brand"><span class="brand-dot"></span>BRIMVALE</div>

  <ul class="benefits">
    <li class="benefit"><svg width="20" height="20" viewBox="0 0 20 20"><circle cx="10" cy="10" r="10" fill="var(--brand-green)"/><path d="M5.5 10.3l3 3 6-6.3" fill="none" stroke="#fff" stroke-width="2.2"/></svg>Don't wait. Protect<br>your home today!</li>
    <li class="benefit"><svg width="20" height="20" viewBox="0 0 20 20"><circle cx="10" cy="10" r="10" fill="var(--brand-green)"/><path d="M5.5 10.3l3 3 6-6.3" fill="none" stroke="#fff" stroke-width="2.2"/></svg>Absolutely free<br>inspection. No<br>obligation.</li>
    <li class="benefit"><svg width="20" height="20" viewBox="0 0 20 20"><circle cx="10" cy="10" r="10" fill="var(--brand-green)"/><path d="M5.5 10.3l3 3 6-6.3" fill="none" stroke="#fff" stroke-width="2.2"/></svg>Termites can cause<br>severe damage to<br>your home</li>
    <li class="benefit"><svg width="20" height="20" viewBox="0 0 20 20"><circle cx="10" cy="10" r="10" fill="var(--brand-green)"/><path d="M5.5 10.3l3 3 6-6.3" fill="none" stroke="#fff" stroke-width="2.2"/></svg>Protect your most<br>valuable asset.</li>
  </ul>

  <div class="website">
    <svg width="22" height="22" viewBox="0 0 22 22" fill="none" stroke="#fff" stroke-width="1.6">
      <circle cx="11" cy="11" r="9.5"/><ellipse cx="11" cy="11" rx="4.2" ry="9.5"/><line x1="1.5" y1="11" x2="20.5" y2="11"/><path d="M3.5 6h15M3.5 16h15"/>
    </svg>
    <span>www.gobrimvale.com</span>
  </div>
</section>

</body>
</html>
```